Business Card Design for Occupational Medicine Start Up Company

We need to design a professional business card. We are a healthcare company providing occupational medicine services to blue collar industries. We are professional, efficient and high quality service providers.

Target Market(s)

Blue Collar Industry: Shipbuilding, Ports, Trucking Companies; The Executives and Safety Officers for these companies

Industry/Entity Type

Healthcare

Contact Information for Business Card

Logo, Name, Title, Email, Phone

Other font styles liked:
• Please match our Brand Guide

Requirements
Must have
• Our Company Colors and Logo

```html
<!DOCTYPE html>
<html lang="en">
<head>
<meta charset="utf-8">
<title>CrewWell Clinics – Business Card</title>
<link rel="stylesheet" href="https://fonts.googleapis.com/css2?family=Montserrat:wght@400;500;600;700&display=swap">
<style>
  :root {
    --stage: #262626;
    --navy: #33307a;
    --sky: #2f9fdc;
    --gold: #f0a93b;
    --paper: #f6f6f4;
    --white: #ffffff;
  }
  * { margin: 0; padding: 0; box-sizing: border-box; }
  html, body {
    width: 1200px; height: 1200px; overflow: hidden;
    background: var(--stage);
    font-family: "Montserrat", sans-serif;
  }
  .canvas { position: relative; width: 1200px; height: 1200px; }
  .card {
    position: absolute; width: 594px; height: 350px;
    border-radius: 24px; overflow: hidden;
  }
  .card-front { left: 298px; top: 198px; background: var(--navy); }
  .card-back { left: 292px; top: 636px; background: var(--paper); }

  .wordmark { position: absolute; text-align: center; font-weight: 700; }
  .wordmark .brand { display: block; font-size: 31px; letter-spacing: 0.5px; line-height: 1; }
  .wordmark .division { display: block; font-size: 16px; letter-spacing: 5px; margin-top: 6px; }
  .card-front .wordmark { left: 30px; top: 262px; color: var(--white); }
  .card-back .wordmark { left: 46px; top: 176px; color: var(--navy); }

  .brand-dot {
    position: absolute; width: 96px; height: 96px; border-radius: 50%;
    background: var(--gold);
  }
  .card-front .brand-dot { left: 410px; top: 90px; width: 150px; height: 150px; }
  .card-back .brand-dot { left: 130px; top: 60px; }

  .wave { position: absolute; left: 0; top: 0; width: 594px; height: 350px; }

  .person { position: absolute; right: 31px; top: 44px; text-align: right; }
  .person .name { font-size: 22px; font-weight: 600; color: var(--sky); letter-spacing: 0.5px; }
  .person .title { font-size: 14px; font-weight: 500; color: var(--navy); margin-top: 2px; }
  .address { position: absolute; right: 31px; top: 112px; text-align: right;
    font-size: 15px; font-weight: 500; color: var(--navy); line-height: 21px; }

  .contacts { position: absolute; right: 30px; top: 258px; list-style: none; }
  .contacts li { display: flex; justify-content: flex-end; align-items: center;
    font-size: 14.5px; color: var(--white); line-height: 21px; }
  .contacts svg { width: 12px; height: 12px; margin-left: 10px; }
</style>
</head>
<body>
<main class="canvas">
  <section class="card card-front" aria-label="Card front">
    <div class="brand-dot"></div>
    <div class="wordmark">
      <span class="brand">CREWWELL</span>
      <span class="division">CLINICS</span>
    </div>
  </section>

  <section class="card card-back" aria-label="Card back">
    <svg class="wave" viewBox="0 0 594 350" aria-hidden="true">
      <path d="M0 292 C110 340 250 330 360 282 C450 242 520 222 594 232 L594 350 L0 350 Z" fill="var(--navy)"/>
      <path d="M50 278 C180 300 300 285 400 248 C480 220 540 208 594 212" fill="none" stroke="var(--sky)" stroke-width="6"/>
      <path d="M0 272 C90 280 200 300 290 300 C210 312 100 312 0 300 Z" fill="var(--gold)"/>
    </svg>
    <div class="brand-dot"></div>
    <div class="wordmark">
      <span class="brand">CREWWELL</span>
      <span class="division">CLINICS</span>
    </div>
    <div class="person">
      <p class="name">DANA HOLT</p>
      <p class="title">Senior Doctor</p>
    </div>
    <p class="address">48 Harbor Lane, Suite 210<br>Portside, State 54321</p>
    <ul class="contacts">
      <li>555-201-4478
        <svg viewBox="0 0 12 12"><path d="M1 4 Q6 0 11 4 L9 6 L7.5 4.5 L4.5 4.5 L3 6 Z M3 6 L9 6 L10 11 L2 11 Z" fill="var(--sky)"/></svg>
      </li>
      <li>www.crewwellclinics.com
        <svg viewBox="0 0 12 12"><rect x="0.5" y="2" width="11" height="8" fill="var(--white)"/><path d="M0.5 2 L6 7 L11.5 2" fill="none" stroke="var(--navy)" stroke-width="1"/></svg>
      </li>
      <li>dana@crewwellclinics.com
        <svg viewBox="0 0 12 12"><circle cx="6" cy="6" r="5.5" fill="var(--gold)"/><path d="M0.5 6 H11.5 M6 0.5 V11.5" stroke="var(--navy)" stroke-width="0.8"/></svg>
      </li>
    </ul>
  </section>
</main>
</body>
</html>
```